Dynamic Business Card for Sports Supplements Company

Hi! I'm looking for an awesome business card to match my existing sports supplement company. I have uploaded my current company logo and screenshot of the front page of my website.

I would like to have something dynamic and interesting and utilize the colors in the website - the reds and purples

The business card should be double sided and focus on a unique eye-catching design on the back and include all the relevant company info.

Most importantly, it should say somewhere: "Sign up on our website for a coupon code."

Target Market(s)

Mostly for women gym goers but it shouldn't be too feminine. It should be in keeping with the website design. It should flow and clearly be connected to it

Industry/Entity Type

Business

Contact Information for Business Card

Lorraine K. Vestal
CEO
LVestal@Quorvanexco.com
www.quorvanexco.com
555.417.3820
P.O. Box 47315
Burke, Virginia 00000

Sign up on our website for a coupon code

Font styles to use
Serif
Sans Serif
Other font styles liked:
• Novecento font family and "Quorvanex" is in AR Destine font

Requirements
Must have
• One side should be a bold Quorvanex logo design. Even just the symbol itself may be o.k. (see attached file)

```html
<!DOCTYPE html>
<html lang="en">
<head>
<meta charset="utf-8">
<title>Quorvanex Business Card</title>
<link rel="stylesheet" href="https://fonts.googleapis.com/css2?family=PT+Sans:ital,wght@0,400;0,700;1,400&display=swap">
<style>
  :root {
    --backdrop: #54463a;
    --card: #000000;
    --accent: #e3202a;
    --ink: #ffffff;
    --muted: #b9b9b9;
    --faint: #1c1c1c;
    --faint-red: #1d0507;
  }
  * { margin: 0; padding: 0; box-sizing: border-box; }
  html, body {
    width: 1200px; height: 987px; overflow: hidden;
    background: var(--backdrop);
    font-family: "PT Sans", "Myriad Pro", Arial, sans-serif;
    color: var(--ink);
  }
  .card {
    position: absolute; left: 293px; width: 615px; height: 351px;
    background: var(--card);
    box-shadow: 0 2px 6px rgba(0,0,0,0.35);
    overflow: hidden;
  }
  .card--front { top: 130px; }
  .card--back { top: 505px; }

  .brand { position: absolute; text-align: center; }
  .brand__mark {
    display: block; width: 78px; height: 78px; margin: 0 auto 12px;
    background: var(--accent);
  }
  .brand__name {
    font-weight: 700; font-size: 33px; letter-spacing: 1.5px; line-height: 1;
    color: var(--ink); text-transform: uppercase;
  }
  .brand__tagline {
    font-size: 10px; letter-spacing: 2.9px; color: var(--muted);
    text-transform: uppercase; margin-top: 4px; white-space: nowrap;
  }
  .card--front .brand { left: 356px; top: 38px; width: 230px; }

  .holder { position: absolute; left: 37px; top: 204px; }
  .holder__name {
    font-weight: 700; font-size: 22px; color: var(--accent);
    text-transform: uppercase; letter-spacing: 0.3px; line-height: 1;
  }
  .holder__title { font-size: 17px; margin-top: 8px; line-height: 1; }
  .divider {
    position: absolute; left: 37px; top: 263px; width: 544px; height: 1px;
    background: var(--ink);
  }
  .contact {
    position: absolute; left: 37px; top: 272px; width: 560px;
    display: flex; gap: 12px; font-size: 17px; white-space: nowrap;
  }
  .contact__item { display: flex; align-items: center; gap: 5px; }
  .contact__item svg { width: 15px; height: 15px; fill: var(--accent); flex: none; }
  .address { position: absolute; left: 37px; top: 301px; font-size: 17px; }

  .back-decoration {
    position: absolute; left: 12px; top: 12px; width: 322px; height: 322px;
    background: linear-gradient(180deg, var(--faint-red) 0%, var(--faint) 55%);
  }
  .card--back .brand { left: 355px; top: 266px; width: 240px; text-align: left; }
  .coupon { font-style: italic; font-size: 13px; margin-top: 4px; white-space: nowrap; }
</style>
</head>
<body>
  <section class="card card--front">
    <div class="brand">
      <span class="brand__mark"></span>
      <div class="brand__name">Quorvanex</div>
      <div class="brand__tagline">Your Endurance Companion</div>
    </div>

    <div class="holder">
      <div class="holder__name">Lorraine K. Vestal</div>
      <div class="holder__title">CEO</div>
    </div>
    <div class="divider"></div>

    <div class="contact">
      <span class="contact__item">
        <svg viewBox="0 0 24 24" aria-hidden="true"><path d="M6.6 10.8a15.1 15.1 0 0 0 6.6 6.6l2.2-2.2a1 1 0 0 1 1-.25 11.4 11.4 0 0 0 3.6.57 1 1 0 0 1 1 1V20a1 1 0 0 1-1 1A17 17 0 0 1 3 4a1 1 0 0 1 1-1h3.5a1 1 0 0 1 1 1c0 1.25.2 2.45.57 3.57a1 1 0 0 1-.25 1z"/></svg>
        555.417.3820
      </span>
      <span class="contact__item">
        <svg viewBox="0 0 24 24" aria-hidden="true"><path d="M2 5h20v14H2z M2 5l10 8 10-8" stroke="#000" stroke-width="1.6"/></svg>
        LVestal@Quorvanexco.com
      </span>
      <span class="contact__item">
        <svg viewBox="0 0 24 24" aria-hidden="true"><circle cx="12" cy="12" r="10"/><path d="M2 12h20M12 2c3 3 3 17 0 20M12 2c-3 3-3 17 0 20" stroke="#000" stroke-width="1.4" fill="none"/></svg>
        quorvanexco.com
      </span>
    </div>
    <div class="address">P.O. Box 47315, Alder Falls, Oregon 00000</div>
  </section>

  <section class="card card--back">
    <div class="back-decoration" role="img" aria-label="Large faint brand decoration area"></div>
    <div class="brand">
      <div class="brand__name">Quorvanex</div>
      <div class="brand__tagline">Your Endurance Companion</div>
      <div class="coupon">Sign up on our website for a coupon code</div>
    </div>
  </section>
</body>
</html>
```